KVR - Redesign (PSD Files Only)

Requirements for the site:

1. We need our logo recreated, please use the same design and change colors to work on a white background

2. The site is a "Wizard" based site, that takes the customer through the process of creating a unique web presence that suits there needs

3.Colors Needed - Main "Dark Blue" Secondary = "Dark Grey" -Other = "Light Grey and White"

4.We need a CRISP CLEAN DESIGN, simple design

5.Wireframes are a general layout and may be modified by you to enhance the design

6. We want a complete web 5.0 look with big buttons and text boxes

7.The more personality the better

8. Current Site brightpolehub.example

9.See attachments for wireframes

10. Designer should deliver PSD files, no coding is required

11. The portfolio wireframe, should look like the design of the artflockly portfolio template
Updates

KEEP IT SIMPLE.,.....

We like the quillmark scaffold style of designs

```html
<!DOCTYPE html>
<html lang="en">
<head>
<meta charset="utf-8">
<title>KVR – Describe Your Project</title>
<link href="https://fonts.googleapis.com/css2?family=Dosis:wght@400;500;600;700&family=Open+Sans:ital,wght@0,400;1,400&display=swap" rel="stylesheet">
<style>
:root{
  --navy:#003764;
  --navy-deep:#0a3a62;
  --header-blue:#0c4d7c;
  --ink:#1e1e1e;
  --bar:#1b1b1b;
  --panel:#ffffff;
  --page-grey:#d4d4d4;
  --rule:#e3e3e3;
  --orange:#ff7a0a;
  --orange-light:#ffa640;
  --muted:#8a8a8a;
}
*{margin:0;padding:0;box-sizing:border-box}
html,body{width:1200px;height:1059px;overflow:hidden}
body{position:relative;background:var(--page-grey);font-family:"Open Sans",sans-serif}
.abs{position:absolute}
.top-strip{left:0;top:0;width:1200px;height:24px;background:var(--bar)}
.hero{left:0;top:24px;width:1200px;height:150px;background:radial-gradient(ellipse at 50% 100%,#0a5a8c 0%,var(--header-blue) 40%,#083a62 100%)}
.navbar{left:129px;top:0;width:942px;height:46px;background:var(--bar)}
.brand{left:151px;top:8px;font-family:"Dosis",sans-serif;font-weight:700;font-size:24px;color:#fff;letter-spacing:1px}
.nav a{position:absolute;top:0;height:46px;line-height:46px;font-family:"Dosis",sans-serif;font-size:21px;font-weight:500;color:#fff;text-decoration:none}
.nav .active{background:#15457a;color:#d7e8f7;padding:0 13px}
.social circle{fill:#fff}
.phone{font-family:"Dosis",sans-serif;font-weight:400;color:#fff;display:flex;align-items:center;gap:4px}
.step{left:0;width:1200px;top:70px;text-align:center;font-size:15px;color:#fff}
.title{left:0;width:1200px;top:88px;text-align:center;font-family:"Dosis",sans-serif;font-weight:700;font-size:34px;color:#fff}
.title span{display:inline-block;vertical-align:middle;width:46px;border-top:3px dotted #fff;margin:0 14px}
.panel{left:129px;top:174px;width:942px;height:651px;background:var(--panel);border-left:1px solid #c8c8c8;border-right:1px solid #c8c8c8}
.crumbs{left:171px;top:193px;font-size:13px;color:var(--navy);display:flex;gap:10px}
.crumbs .off{color:var(--muted)}
.crumb-rule{left:129px;top:225px;width:942px;height:1px;background:var(--rule)}
.field{left:165px;top:267px;width:600px;height:223px;border:1px solid #cfcfcf;border-radius:2px;box-shadow:inset 3px 3px 4px rgba(0,0,0,.08);padding:12px 14px;font-size:13px;color:#666}
.btn{background:linear-gradient(var(--orange-light),var(--orange));font-family:"Dosis",sans-serif;font-weight:700;color:#fff;text-align:center;border:1px solid #f07000}
.note{left:523px;top:561px;width:250px;font-size:15.5px;line-height:19px;color:var(--navy)}
.info{left:154px;top:733px;width:891px;height:63px;background:var(--navy);border:1px solid #0b4f86;display:flex;align-items:center;padding-left:16px;gap:14px}
.info p{font-style:italic;font-size:15.5px;line-height:18px;color:#fff;width:810px}
.footer{left:0;top:825px;width:1200px;height:234px;background:var(--ink)}
.flinks{left:129px;top:866px;font-size:13px;color:#fff;line-height:19px}
.strip{left:129px;top:948px;width:948px;height:55px;background:#1a1a1a}
.badge{left:129px;top:948px;width:156px;height:54px;background:#f4f4f4;border-left:54px solid #3f7be0}
</style>
</head>
<body>
<div class="abs top-strip"></div>
<div class="abs hero"></div>
<header class="abs navbar"></header>
<div class="abs brand">KVR</div>
<nav class="nav">
  <a style="left:235px">Home</a>
  <a class="active" style="left:295px">About Us</a>
  <a style="left:405px">Portfolio</a>
  <a style="left:489px">Contact Us</a>
</nav>
<svg class="abs social" style="left:703px;top:9px" width="130" height="28" aria-label="Social links"><circle cx="14" cy="14" r="13"/><circle cx="48" cy="14" r="13"/><circle cx="81" cy="14" r="13"/><circle cx="114" cy="14" r="13"/></svg>
<div class="abs phone" style="left:883px;top:7px;font-size:26px">
  <svg width="14" height="20" viewBox="0 0 14 20"><path d="M3 1l3 1 1 5-2 1c1 3 2 5 4 7l2-1 3 3-1 2c-2 1-5 0-7-3S1 8 1 4z" fill="#fff"/></svg>1800-555-0142
</div>
<div class="abs step">STEP 3</div>
<h1 class="abs title"><span></span>Describe Your Project<span></span></h1>
<svg class="abs" style="left:588px;top:162px" width="24" height="13"><path d="M0 13L12 0 24 13z" fill="#fff"/></svg>

<main class="abs panel"></main>
<div class="abs crumbs"><span>Level 1</span><span>»</span><span>Level 2</span><span>»</span><span>Level 3</span><span>»</span><span class="off">Level 4</span></div>
<div class="abs crumb-rule"></div>
<svg class="abs" style="left:797px;top:176px" width="92" height="92" aria-label="Progress gauge">
  <circle cx="46" cy="46" r="45" fill="#fff"/>
  <circle cx="46" cy="46" r="32" fill="none" stroke="#e4e4e4" stroke-width="12"/>
  <path d="M14 46A32 32 0 0 1 46 14" fill="none" stroke="var(--navy)" stroke-width="12"/>
  <path d="M44 46L46 22 48 46z" fill="#111"/><circle cx="46" cy="46" r="4" fill="#8aa8c8" stroke="#111" stroke-width="1.5"/>
</svg>
<div class="abs field">Please explain any additional information, needed to give an accurate quote.</div>
<div class="abs btn" style="left:522px;top:503px;width:243px;height:55px;line-height:53px;font-size:27px">Request Consultant</div>
<p class="abs note">Our web professionals will contact you to discuss your project</p>
<div class="abs info">
  <svg width="30" height="30"><circle cx="15" cy="15" r="14" fill="#fff"/><text x="15" y="22" text-anchor="middle" font-family="Georgia,serif" font-style="italic" font-weight="700" font-size="19" fill="var(--navy)">i</text></svg>
  <p>We are a full service web marketing company and meet any request. No project is large or small. We have a team of experts that can build the site that suits your needs.</p>
</div>

<footer class="abs footer"></footer>
<div class="abs flinks">Home &nbsp;. &nbsp;About Us &nbsp;. &nbsp;Portfolio &nbsp;. &nbsp;Contact Us<br>Copyright © 2014 Kavro Studios Inc - All Right Reserved<br>www.brightpolehub.example</div>
<svg class="abs social" style="left:497px;top:862px" width="178" height="40" aria-label="Social links"><circle cx="20" cy="20" r="19"/><circle cx="66" cy="20" r="19"/><circle cx="111" cy="20" r="19"/><circle cx="157" cy="20" r="19"/></svg>
<div class="abs phone" style="left:498px;top:905px;font-size:26px">
  <svg width="14" height="20" viewBox="0 0 14 20"><path d="M3 1l3 1 1 5-2 1c1 3 2 5 4 7l2-1 3 3-1 2c-2 1-5 0-7-3S1 8 1 4z" fill="#fff"/></svg>1800-555-0142
</div>
<div class="abs btn" style="left:828px;top:862px;width:243px;height:55px;line-height:53px;font-size:27px">Request Consultant</div>
<div class="abs strip"></div>
<div class="abs badge" role="img" aria-label="Partner badge"></div>
</body>
</html>
```